Tea Shop - Drinks Menu - Vertical TV screen

Need a drinks menu design for a tea shop based in The Netherlands. Called BrewHaven.
Currently we are trying to attract more customers for our Cup4Road and the idea came up to place 3 TV screen vertically in order to use 2 for the menu.
Website: http://brewhaven-dorpsplein.example/
Posible colour themes -
- Light green (same green as logo)
- Light brown
Dimensions of the screen -
- 40inch
- 905 mm Height
- 207 mm Width
Resolution of the menu must be 1920x1080 BUT VERTICAL
Needs to contain the following -
- Hot Cup4Road
- BLACK
- Delicate Velvet Dusk
- Sweet Papaya Hug
- Plummy Orchard
- Spicy Chai
- Black Assam
- Duke of Highbrook
- Smokey Lapsang Suochong
- ( and many more teas, so leave space for aditional 5+)
- GREEN
- Sencha Kiwi-Clove
- Sencha Meadow Cherries
- Sencha Melon Toffee
- Bright Lotus
- Bancha
- Classic Cloudburst
- (space for aditional 4+)
- OOLONG
- Pebble Oolong
- Creamy Oolong
- WHITE
- Bai Mu Tan
- HERBAL
- BrewHaven's Dream
- Refreshing Linden
- Pure Ginger
- Moon Blend
- Lulu Sage
- Thyme Blueberry
- FRUIT TEA
- Zesty Walnut
- Jolly Berry
- Guava Hug
- Zingy Quince
- Sunset Plum
- (space for aditional 2+)
- LATTÉ
- Spiced Chai
- Green Chai
- Vanille Chai
- Matcha
- Fresh Mint tea
- Iced Tea
- Peach
- Raspberry
- Lemon
- Mango
Divide this menu over 2 TV screens with the mentioned dimensions and use the font provided in the uploaded files (not mandatory if you think you have a bette idea).
Simple
Needs to attract people
Easy to adjust
Idea's are always welcome and appreciated
LOGO LINK : http://img42.picvault.example/8qz4rk1.png
(image too big to upload on here, sorry)
people whom drink TEA
Tv

```html
<!DOCTYPE html>
<html lang="en">
<head>
<meta charset="utf-8">
<title>BrewHaven – Drinks Menu Screen 2</title>
<link rel="stylesheet" href="https://fonts.googleapis.com/css2?family=Ubuntu:wght@300;400&display=swap">
<style>
  :root {
    --menu-orange: #ba6628;
    --photo-light: #e6c7a3;
    --photo-warm: #cf8f55;
    --photo-deep: #8a5a3a;
    --herbal-green: #5b8f49;
    --fruit-gold: #dcae58;
    --fruit-text: #fbf1d6;
    --latte-yellow: #e0b422;
    --mint-purple: #7b5b78;
    --bullet-grey: #b7b2ad;
    --bullet-lime: #a8c52a;
    --bullet-white: #ffffff;
    --bullet-plum: #a0288a;
    --text-light: #fdf6ee;
  }
  html, body {
    margin: 0;
    padding: 0;
    width: 1200px;
    height: 5237px;
    overflow: hidden;
    background: var(--menu-orange);
  }
  .menu-screen {
    position: relative;
    width: 1200px;
    height: 5237px;
    overflow: hidden;
    background: var(--menu-orange);
    font-family: "Ubuntu", sans-serif;
    font-weight: 300;
    color: var(--text-light);
  }
  .photo-top {
    position: absolute;
    left: 0; top: 0;
    width: 1200px; height: 1150px;
    background:
      radial-gradient(ellipse 420px 260px at 600px 380px, rgba(205,180,140,0.55), transparent 70%),
      linear-gradient(180deg, var(--photo-light) 0%, #d6a677 45%, rgba(186,102,40,0) 100%);
  }
  .photo-bottom {
    position: absolute;
    left: 0; top: 3050px;
    width: 1200px; height: 2187px;
    background:
      radial-gradient(ellipse 520px 700px at 860px 1250px, rgba(110,70,45,0.45), transparent 70%),
      linear-gradient(180deg, rgba(186,102,40,0) 0%, var(--photo-warm) 30%, #c99a6e 70%, #d8b38c 100%);
  }
  .category-label {
    position: absolute;
    left: 148px;
    height: 166px;
    margin: 0;
    display: flex;
    align-items: center;
    font-weight: 400;
    line-height: 1;
  }
  .label-herbal {
    top: 692px; width: 627px;
    background: var(--herbal-green);
    padding-left: 34px; box-sizing: border-box;
    font-size: 140px; color: #fff;
  }
  .label-fruit {
    top: 2083px; width: 627px;
    background: var(--fruit-gold);
    justify-content: center;
    font-size: 100px; color: var(--fruit-text);
  }
  .label-latte {
    top: 3147px; width: 627px;
    background: var(--latte-yellow);
    padding-left: 128px; box-sizing: border-box;
    font-size: 100px; color: #fff;
  }
  .label-mint {
    top: 3962px; width: 889px;
    background: rgba(123,91,120,0.85);
    padding-left: 130px; box-sizing: border-box;
    font-size: 100px; color: #fff;
  }
  .tea-list {
    position: absolute;
    left: 0;
    margin: 0;
    padding: 0;
    list-style: none;
    font-size: 100px;
  }
  .tea-list li {
    position: relative;
    height: 114px;
    line-height: 114px;
    white-space: nowrap;
  }
  .tea-list li::before {
    content: "";
    position: absolute;
    top: 34px;
    width: 46px; height: 46px;
    border-radius: 50%;
  }
  .list-herbal { top: 922px; }
  .list-herbal li { padding-left: 210px; }
  .list-herbal li::before { left: 71px; background: var(--bullet-grey); }
  .list-fruit { top: 2305px; }
  .list-fruit li { padding-left: 210px; }
  .list-fruit li::before { left: 69px; background: var(--bullet-lime); }
  .list-latte { top: 3353px; }
  .list-latte li { padding-left: 212px; height: 117px; line-height: 117px; }
  .list-latte li::before { left: 95px; background: var(--bullet-white); }
  .list-mint { top: 4230px; }
  .list-mint li { padding-left: 230px; height: 116px; line-height: 116px; }
  .list-mint li::before { left: 103px; background: var(--bullet-plum); }
</style>
</head>
<body>
<main class="menu-screen">
  <div class="photo-top" role="img" aria-label="Photo of a hand scooping loose leaf tea into a paper bag"></div>
  <div class="photo-bottom" role="img" aria-label="Photo of an iced tea in a takeaway cup with a pink straw and BrewHaven sleeve"></div>

  <h2 class="category-label label-herbal">HERBAL</h2>
  <ul class="tea-list list-herbal">
    <li>BrewHaven's Dream</li>
    <li>Refreshing Linden</li>
    <li>Pure Ginger</li>
    <li>Moon Blend</li>
    <li>Lulu Sage</li>
    <li>Thyme Blueberry</li>
    <li></li>
    <li></li>
    <li></li>
    <li></li>
  </ul>

  <h2 class="category-label label-fruit">FRUIT TEA</h2>
  <ul class="tea-list list-fruit">
    <li>Zesty Walnut</li>
    <li>Jolly Berry</li>
    <li>Guava Hug</li>
    <li>Zingy Quince</li>
    <li>Sunset Plum</li>
    <li></li>
    <li></li>
  </ul>

  <h2 class="category-label label-latte">LATTÉ</h2>
  <ul class="tea-list list-latte">
    <li>Spiced Chai</li>
    <li>Green Chai</li>
    <li>Vanille Chai</li>
    <li>Matcha</li>
  </ul>

  <h2 class="category-label label-mint">Fresh Mint tea</h2>
  <ul class="tea-list list-mint">
    <li>Iced Tea</li>
    <li>Peach</li>
    <li>Raspberry</li>
    <li>Lemon</li>
    <li>Mango</li>
  </ul>
</main>
</body>
</html>
```